Letterhead for a German Distribution/Manufacturing Company

We need a professional Letterhead in a unique Design.
not to playful.
The Letterhead has to show show that we are a international company with headquater in Germany.
all details like adress, Vat Tax Number, Bank Accout, Eori, email, Company number has to be on the Letterhead.
for example use: VAT TAX DE5470318 Bank Account: Kestrel Bank IBAN DE412058731ß204683 Swift: MORV0417352 EORI 3150428697 Company Number: HRB 51806 Adress: VOLMINTA UG Ahornweg 7 Postal Code 06384 City Talbrück Country: Germany Email: info@volminta-example.com
the design can be colored but doesnt have to be
Industry/Entity Type
Manufacturing and international distribution
Requirements
Must have
- show that we are a international company with headquater in Germany. our company infos and logo

```html
<!DOCTYPE html>
<html lang="en">
<head>
<meta charset="utf-8">
<title>Volminta Letterhead</title>
<link rel="stylesheet" href="https://fonts.googleapis.com/css2?family=Lato:wght@400;700&family=Dancing+Script:wght@500&display=swap">
<style>
  :root {
    --backdrop: #e4e4e4;
    --paper: #ffffff;
    --band: #515151;
    --band-text: #ffffff;
    --ink: #2b2b2b;
    --ink-soft: #444444;
  }
  * { box-sizing: border-box; margin: 0; padding: 0; }
  html, body {
    width: 1200px; height: 874px; overflow: hidden;
    background: var(--backdrop);
  }
  .letterhead {
    position: absolute; left: 306px; top: 22px;
    width: 588px; height: 830px;
    background: var(--paper);
    font-family: "Lato", sans-serif;
    color: var(--ink);
    box-shadow: 0 2px 10px rgba(0,0,0,0.12);
  }
  .masthead {
    height: 132px; background: var(--band);
    display: flex; align-items: center;
    padding: 0 0 0 40px;
  }
  .brand {
    display: flex; align-items: center; gap: 12px;
    width: 270px;
    color: var(--band-text);
    font-size: 25px; font-weight: 400; letter-spacing: 1.5px;
  }
  .brand-dot {
    width: 26px; height: 26px; border-radius: 50%;
    background: var(--band-text);
  }
  .company-details {
    border-left: 1px solid var(--band-text);
    padding: 4px 0 4px 12px;
    color: var(--band-text);
    font-size: 7.4px; font-weight: 400; line-height: 1.45; letter-spacing: 0.2px;
  }
  .letter {
    padding: 44px 52px 0 56px;
    font-size: 10.5px; line-height: 1.4;
  }
  .letter-date { margin-bottom: 16px; }
  .recipient { margin-bottom: 14px; }
  .recipient-company { margin-bottom: 18px; }
  .salutation { font-weight: 700; font-size: 13px; margin-bottom: 14px; }
  .letter p.body-text { margin-bottom: 18px; color: var(--ink-soft); }
  .closing { margin-top: 22px; font-size: 9.5px; color: var(--ink-soft); }
  .signature {
    font-family: "Dancing Script", cursive;
    font-size: 34px; font-weight: 500;
    margin: 10px 0 0 30px; color: #1e1e1e;
  }
</style>
</head>
<body>
  <article class="letterhead">
    <header class="masthead">
      <div class="brand"><span class="brand-dot"></span><span class="brand-name">VOLMINTA</span></div>
      <div class="company-details">
        VAT TAX DE5470318<br>
        Bank Account: Kestrel Bank IBAN DE412058731ß204683<br>
        Swift: MORV0417352<br>
        EORI 3150428697<br>
        Company Number: HRB 51806<br>
        Adress: VOLMINTA UG Ahornweg 7 Postal Code 06384<br>
        City Talbrück Country<br>
        Germany Email: info@volminta-example.com
      </div>
    </header>
    <section class="letter">
      <p class="letter-date">January-03-2020</p>
      <p class="recipient">Mr, Peter Hale<br>President</p>
      <p class="recipient-company">Fenwick Holdings<br>48 Harbor Lane, Suite# 10<br>City, State, 120023</p>
      <p class="salutation">Dear Mr, Peter</p>
      <p class="body-text">Lorem ipsum dolor sit amet, consectetur adipisicing elit, sed do eiusmod tempor incididunt ut labore et dolore magna aliqua. Ut enim ad minim veniam, quis nostrud exercitation ullamco laboris nisi ut aliquip ex ea commodo consequat. Duis aute irure dolor in reprehenderit in voluptate velit esse cillum dolore eu fugiat nulla pariatur.</p>
      <p class="body-text">Lorem ipsum dolor sit amet, consectetur adipisicing elit, sed do eiusmod tempor incididunt ut labore et dolore magna aliqua. Ut enim ad minim veniam, quis nostrud exercitation ullamco laboris nisi ut aliquip ex ea commodo consequat. Duis aute irure dolor in reprehenderit in voluptate velit esse cillum dolore eu fugiat nulla pariatur.</p>
      <p class="body-text">Lorem ipsum dolor sit amet, consectetur adipisicing elit, sed do eiusmod tempor incididunt ut labore et dolore magna aliqua. Ut enim ad minim veniam, quis nostrud exercitation ullamco laboris nisi ut aliquip ex ea commodo consequat.</p>
      <p class="body-text">Excepteur sint occaecat cupidatat non proident, sunt in culpa qui officia deserunt mollit anim id est laborum. re et dolore magnam aliquam quaerat voluptatem.</p>
      <p class="closing">Regards</p>
      <p class="signature">Daniel Weber</p>
    </section>
  </article>
</body>
</html>
```